We need a new business card that reflects who we are. Professional, classy, modern, and service ori

We need a business card design for a window coverings design company in Kansas City called Bright Lane Interiors. We offer professional, modern, and high quality window covering products. We are looking to portray an image of a big, national franchise. We are a 5 location (with showrooms) business with 10 professional designers and 4 professional installers. These cards will be used with Thank you cards, given to realtors, and asked for referrals with.

Target Market(s)

Kansas City

Industry/Entity Type

Business

Contact Information for Business Card

We would like our card to look clean and simple on the front, featuring our logo and Marlow Fenwick's. Our designers' phone numbers and emails should be displayed as well as their title.

Font styles to use
Sans Serif

Colors

Designer to choose colors to be used in the design.

Requirements
Must have
• Front - Logos, name, phone number, email address
• Back - Showroom locations, social media? Appt date/time?
Nice to have
• I would like a clean and modern look (not contemporary. I like a white background, but I am open to ideas. Looking for a "National chain" look for a small business.
Should not have
• Too much busyness.

```html
<!DOCTYPE html>
<html lang="en">
<head>
<meta charset="utf-8">
<title>Bright Lane Interiors – Business Card</title>
<link rel="stylesheet" href="https://fonts.googleapis.com/css2?family=Roboto:wght@400;500;700&family=Roboto+Condensed:wght@500;700&display=swap">
<style>
  :root {
    --backdrop: #2b2b2b;
    --card: #f4f4f4;
    --brand-red: #c9403f;
    --ink: #111111;
    --text-grey: #4a4a4a;
    --rule-grey: #c8c8c8;
    --dot-grey: #7a7a7a;
  }
  * { box-sizing: border-box; margin: 0; padding: 0; }
  html, body {
    width: 1200px; height: 960px; overflow: hidden;
    background: var(--backdrop);
    font-family: "Roboto", Arial, sans-serif;
  }
  .canvas { position: relative; width: 1200px; height: 960px; }

  .card {
    position: absolute; left: 320px; width: 600px;
    background: var(--card);
  }

  /* Front */
  .card--front { top: 100px; height: 352px; }
  .front-accent {
    position: absolute; left: 0; right: 0; bottom: 0; height: 29px;
    background: var(--brand-red);
    border-top: 3px solid var(--ink);
  }
  .brand {
    position: absolute; left: 48px; top: 130px; width: 235px;
    text-align: center;
  }
  .brand-name {
    display: flex; align-items: center; justify-content: center; gap: 8px;
    font-size: 20px; font-weight: 500; color: var(--brand-red);
    letter-spacing: 0.2px;
  }
  .brand-mark { width: 14px; height: 14px; background: var(--brand-red); }
  .brand-tagline {
    margin-top: 8px; font-size: 11.5px; color: var(--ink);
  }
  .divider {
    position: absolute; left: 306px; top: 115px; width: 1px; height: 130px;
    background: var(--rule-grey);
  }
  .person { position: absolute; left: 335px; top: 127px; }
  .person-name {
    font-family: "Roboto Condensed", Arial, sans-serif;
    font-size: 23px; font-weight: 700; color: var(--brand-red);
    line-height: 1;
  }
  .person-title {
    font-family: "Roboto Condensed", Arial, sans-serif;
    margin-top: 3px; font-size: 15px; font-weight: 700; color: var(--ink);
    letter-spacing: 0.3px;
  }
  .contact-list { list-style: none; margin-top: 8px; }
  .contact-list li {
    display: flex; align-items: center; gap: 9px;
    font-size: 14px; color: var(--text-grey); line-height: 19.5px;
  }
  .contact-list svg { width: 12px; height: 12px; fill: var(--brand-red); }

  /* Back */
  .card--back { top: 493px; height: 342px; }
  .back-brand {
    position: absolute; right: 60px; top: 66px;
    display: flex; align-items: center; gap: 8px;
    font-size: 19px; font-weight: 500; color: var(--brand-red);
  }
  .appointment-title {
    position: absolute; left: 43px; top: 87px;
    font-size: 19px; font-weight: 500; color: var(--brand-red);
  }
  .field-row {
    position: absolute; left: 43px; right: 58px;
    display: flex; align-items: baseline;
    font-size: 16px; color: var(--brand-red);
  }
  .field-row--name { top: 139px; }
  .field-row--when { top: 180px; }
  .field-line {
    flex: 1; margin: 0 2px 0 12px;
    border-bottom: 1.5px dotted var(--dot-grey);
    transform: translateY(-3px);
  }
  .field-line--date { flex: 0 0 215px; margin-left: 4px; }
  .field-line--time { flex: 0 0 133px; margin-left: 5px; }
  .field-suffix { font-size: 12px; margin-left: 4px; }
  .locations {
    position: absolute; left: 43px; top: 232px;
    font-size: 14.3px; font-weight: 700; color: var(--text-grey);
    letter-spacing: 0.2px; word-spacing: 1px;
  }
  .social-list {
    position: absolute; left: 44px; top: 279px;
    display: flex; gap: 3px; list-style: none;
  }
  .social-list li {
    width: 22px; height: 22px; border-radius: 50%;
    background: var(--brand-red);
  }
  .partner {
    position: absolute; right: 56px; top: 279px;
    display: flex; align-items: center; gap: 6px;
    font-size: 16px; font-weight: 700; color: var(--text-grey);
  }
  .partner-dot { width: 14px; height: 14px; border-radius: 50%; background: var(--text-grey); }
</style>
</head>
<body>
<main class="canvas">

  <section class="card card--front" aria-label="Business card front">
    <div class="brand">
      <div class="brand-name"><span class="brand-mark"></span>Bright Lane Interiors</div>
      <p class="brand-tagline">Blinds, Shades, Shutters, Draperies &amp; Decor</p>
    </div>
    <div class="divider"></div>
    <div class="person">
      <h1 class="person-name">AVERY COLLINS</h1>
      <p class="person-title">DESIGNER</p>
      <ul class="contact-list">
        <li><svg viewBox="0 0 24 24" aria-hidden="true"><path d="M6.6 10.8a15.1 15.1 0 0 0 6.6 6.6l2.2-2.2c.3-.3.7-.4 1-.2 1.1.4 2.3.6 3.6.6.6 0 1 .4 1 1V20c0 .6-.4 1-1 1A17 17 0 0 1 3 4c0-.6.4-1 1-1h3.5c.6 0 1 .4 1 1 0 1.3.2 2.5.6 3.6.1.3 0 .7-.2 1z"/></svg>913.555.0142</li>
        <li><svg viewBox="0 0 24 24" aria-hidden="true"><path d="M2 5h20v14H2z"/><path d="M3 6l9 6.3L21 6" fill="none" stroke="var(--card)" stroke-width="2"/></svg>info@brightlaneinteriors.com</li>
        <li><svg viewBox="0 0 24 24" aria-hidden="true"><circle cx="12" cy="12" r="10"/><path d="M2 12h20M12 2c3 3 3 17 0 20M12 2c-3 3-3 17 0 20" fill="none" stroke="var(--card)" stroke-width="1.6"/></svg>brightlaneinteriors.com</li>
      </ul>
    </div>
    <div class="front-accent"></div>
  </section>

  <section class="card card--back" aria-label="Business card back">
    <div class="back-brand"><span class="brand-mark"></span>Bright Lane</div>
    <h2 class="appointment-title">Next Appointment</h2>
    <div class="field-row field-row--name">Name :<span class="field-line"></span></div>
    <div class="field-row field-row--when">
      Date :<span class="field-line field-line--date"></span>Time :<span class="field-line field-line--time"></span><span class="field-suffix">AM/PM</span>
    </div>
    <p class="locations">ASHFORD | MAPLE HEIGHTS | CEDAR RIDGE | NORTHGATE | PINE HOLLOW</p>
    <ul class="social-list" aria-label="Social media">
      <li></li><li></li><li></li><li></li>
    </ul>
    <div class="partner">Marlow Fenwick<span class="partner-dot"></span></div>
  </section>

</main>
</body>
</html>
```